Stroll Past Linwood Infographic

Hi I need a color eye catching infographic to market my service/products to tour companies. My business card color are orange and blue. This should be a two-sided document.

```html
<!DOCTYPE html>
<html lang="en">
<head>
<meta charset="utf-8">
<title>Stroll Past Linwood</title>
<link href="https://fonts.googleapis.com/css2?family=Ubuntu:ital,wght@0,400;0,500;0,700;1,700&display=swap" rel="stylesheet">
<style>
  :root{
    --blue:#137ea6;
    --blue-text:#1a7aa6;
    --orange:#f5922a;
    --orange-deep:#ea7a1c;
    --badge-top:#fcc52c;
    --badge-bottom:#ef7f1e;
    --ink:#1e1e1e;
    --grey:#8a8a8a;
    --white:#ffffff;
    --dark:#231f20;
  }
  *{margin:0;padding:0;box-sizing:border-box}
  html,body{width:1200px;height:1000px;overflow:hidden;background:var(--white)}
  body{font-family:"Ubuntu",sans-serif;position:relative;color:var(--white)}

  .brand{position:absolute;left:0;width:1200px;top:22px;display:flex;flex-direction:column;align-items:center;gap:6px}
  .brand-dot{width:30px;height:30px;border-radius:50%;background:var(--orange)}
  .brand-name{font-size:14px;font-weight:400;color:var(--blue);letter-spacing:.3px;text-transform:uppercase}

  .pledge{position:absolute;left:0;width:1212px;top:75px;text-align:center;color:var(--grey);font-size:14.5px;font-weight:500;line-height:19px}

  .hero{position:absolute;left:212px;top:132px;width:774px;height:233px;background:var(--orange)}
  .hero-fold{position:absolute;left:0;top:0}
  .hero-copy{position:absolute;left:0;top:8px;width:774px;text-align:center;font-size:14px;line-height:19px;padding:0 6px}
  .hero-copy em{font-weight:700;font-style:italic}
  .hero-copy .aside{margin-top:6px}

  .pill{position:absolute;width:178px;height:22px;border-radius:11px;background:var(--white);color:var(--blue-text);font-size:14.5px;font-weight:500;text-align:center;line-height:22px;box-shadow:0 2px 4px rgba(0,0,0,.35)}
  .explore{position:absolute;left:262px;top:153px}
  .explore-label{position:absolute;left:262px;top:153px;width:264px;height:36px;line-height:36px;text-align:center;font-size:14px;color:var(--white)}

  .offer{position:absolute;left:222px;width:755px}
  .offer-tab{height:28px;background:var(--orange);border-radius:12px 12px 0 0;color:var(--ink);font-weight:700;font-size:15px;padding-left:14px;line-height:31px}
  .offer-body{background:var(--blue);font-size:14px;line-height:20px;padding:3px 12px 6px}
  .offer-body p{line-height:18px;margin-bottom:1px}
  .checks{list-style:none;padding-left:75px}
  .checks li{position:relative;padding-left:22px;line-height:18.5px;margin-bottom:1.5px}
  .checks li::before{content:"";position:absolute;left:0;top:2px;width:15px;height:15px;border-radius:50%;background:#e9e9e9;box-shadow:inset 0 -1px 2px rgba(0,0,0,.3)}
  .checks li::after{content:"";position:absolute;left:5px;top:5px;width:3px;height:6px;border:solid #3a3a3a;border-width:0 2px 2px 0;transform:rotate(40deg)}

  .badge{position:absolute;width:72px;height:72px;border-radius:50%;background:radial-gradient(circle at 50% 25%,var(--badge-top),var(--badge-bottom) 75%);box-shadow:0 2px 4px rgba(0,0,0,.4);color:var(--ink);font-size:13.5px;line-height:17px;text-align:center;padding-top:16px;overflow:hidden}
  .badge::after{content:"";position:absolute;left:14px;bottom:-10px;width:44px;height:18px;border-radius:50%;background:var(--white)}
</style>
</head>
<body>

<header class="brand">
  <span class="brand-dot"></span>
  <span class="brand-name">Stroll Past Linwood</span>
</header>

<p class="pledge">If you only learn one thing about us today, it should be this:<br>We LOVE Linwood and are VERY proud of our neighborhood!<br>This is why we do what we do.</p>

<section class="hero">
  <svg class="hero-fold" width="774" height="125" viewBox="0 0 774 125" aria-hidden="true">
    <polygon points="0,0 774,0 774,70 388,120 0,73" fill="var(--blue)"/>
  </svg>
  <div class="hero-copy">
    <p>“<em>Stroll Past Linwood</em>” is a New York City Certified Minority and Women-Owned Business.&nbsp; We are a full service tour company responding to what is happening in Linwood. We celebrate our cultural diversity through music, dance, theater, and dining.</p>
    <p class="aside">There's so much about Linwood that you can learn. But don't worry. We're here to help!</p>
  </div>

  <span class="pill" style="left:72px;top:121px">Tours</span>
  <span class="pill" style="left:72px;top:147px">Educational Tours</span>
  <span class="pill" style="left:72px;top:172px">Live Entertainment</span>
  <span class="pill" style="left:72px;top:198px">Fine Dining</span>

  <svg class="explore" width="264" height="36" viewBox="0 0 264 36" aria-hidden="true">
    <polygon points="12,0 252,0 264,18 252,36 12,36 0,18" fill="var(--dark)"/>
  </svg>
  <span class="explore-label">Explore Linwood with us through:</span>

  <span class="pill" style="left:539px;top:120px">Theater</span>
  <span class="pill" style="left:539px;top:146px">Linwood Pop-Up-Shop</span>
  <span class="pill" style="left:539px;top:172px">Vaudeville</span>
  <span class="pill" style="left:539px;top:198px">Host of special events</span>
</section>

<section class="offer" style="top:422px">
  <h2 class="offer-tab">Tours</h2>
  <div class="offer-body" style="height:166px">
    <ul class="checks">
      <li>Hop on Guides</li>
      <li>Walking Tours</li>
      <li>Custom Tours</li>
      <li>Gospel and brunch tours</li>
      <li>Educational tours for students, senior groups, family reunions, businesses and organizations<br>no group is too big or too small.</li>
      <li>We arrange tours with and without meals</li>
      <li>Looking for a church to bring your clients? We can help</li>
    </ul>
  </div>
</section>
<div class="badge" style="left:894px;top:382px">Starting<br>at $10</div>

<section class="offer" style="top:664px">
  <h2 class="offer-tab">Music</h2>
  <div class="offer-body" style="height:143px">
    <p>Trust our colorful and enticing palette filled with jazz, gospel, Latin jazz, South African music and so much more. You are sure to be entertained and enlightened!</p>
    <ul class="checks">
      <li>Jazz concerts– afternoon and evening sessions</li>
      <li>Gospel concerts starting</li>
      <li>Introduction to music for students</li>
      <li>Special events</li>
      <li>Special private concerts for large groups (call ahead to arrange)</li>
    </ul>
  </div>
</section>
<div class="badge" style="left:894px;top:624px">Starting<br>at $15</div>

<section class="offer" style="top:880px">
  <h2 class="offer-tab">Linwood Pop-Up-Shop</h2>
  <div class="offer-body" style="height:71px;padding-top:6px">
    <p>For the true shoponista's time to discover our hidden treasures and shop Linwood! If you truly want to top off your visit here then pop into our Linwood Pop-Up-Shop. A collection of local artists with unique and one-of-a-kind discoveries waiting for you.</p>
  </div>
</section>
<div class="badge" style="left:893px;top:841px">$7 per<br>person</div>

</body>
</html>
```